Company website for an international IT business

We require a website for our business, Korvel Solutions. The business has two primary areas: Lanterns, which includes two machine learning/deep learning based products and IT consultancy, which is the service we provide to other businesses.

We bridge cutting-edge research to market.

STYLING:
The site can be on single page or multi-page. This is fully open to suggestion. So long as the look and feel are consistent. Currently, we have no strong preference for colors, styles or layouts.
You can find the logo of our website in the attachment “Korvel-logo.png” and “Korvel-logo-landscape.png”.

CONTENT:
You can find the text of the website in “Website-Content.pdf”, which explains the services and products of our business. The format of the text is also open to suggestion - including breaking up the text into visually appealing sections.
We would also like to include suitable images on the website so that it does not appear to be a text-heavy page. We are happy to have placeholder images on stock image sites if needed. We are open to suggestions on placing of images

ATTACHMENT:

Industry/Entity Type

It Company

Coding

Coded - Design and coding required

Number of Pages Required

1 page

Colors

Designer to choose colors to be used in the design.

Requirements
Must have
• A full description of the requirement is in the attachment "Website-Content.pdf"
• The design must have HTML/CSS, and all resources relevant (images, fonts etc)
• We are
Nice to have
• We are open to suggestions on top of the requirement, please reach out and communicate.

```html
<!DOCTYPE html>
<html lang="en">
<head>
<meta charset="utf-8">
<title>Korvel Solutions</title>
<link href="https://fonts.googleapis.com/css2?family=Montserrat:wght@700;800;900&family=Open+Sans:wght@400;600;700;800&family=Poppins:wght@300;400;500;600&display=swap" rel="stylesheet">
<style>
:root{
  --blue:#1d8fd6;
  --blue-dark:#0f6fb0;
  --ink:#1b1b1b;
  --grey:#8a8a8a;
  --light:#f2f2f2;
  --dark:#2a2a2a;
  --white:#ffffff;
}
*{margin:0;padding:0;box-sizing:border-box}
html,body{width:1200px;height:4423px;overflow:hidden}
body{position:relative;background:var(--white);font-family:"Poppins",sans-serif;color:var(--ink)}
.abs{position:absolute}
.wide{font-family:"Montserrat",sans-serif;font-weight:900;letter-spacing:4px;text-transform:uppercase}
.blue{color:var(--blue)}

/* header */
.header{top:0;left:0;width:1200px;height:127px;background:var(--white)}
.brand{left:82px;top:18px;display:flex;align-items:center;gap:14px}
.brand-mark{width:80px;height:80px;border-radius:50%;background:var(--blue)}
.brand-name{font-family:"Open Sans",sans-serif;font-weight:800;font-size:30px;letter-spacing:2px;color:var(--ink)}
.contact-line{top:18px;display:flex;align-items:center;gap:12px;font-size:15px;color:var(--grey)}
.contact-line .ring{width:38px;height:38px;border:2px solid var(--blue);border-radius:50%;display:flex;align-items:center;justify-content:center}
.nav{top:82px;left:433px;display:flex;gap:0;font-size:16px;color:#a4a4a4}
.nav a{color:inherit;text-decoration:none;display:block;padding-bottom:12px}
.nav a.active{color:var(--blue);border-bottom:3px solid var(--blue)}

/* hero */
.hero{top:127px;left:0;width:1200px;height:551px;background:linear-gradient(180deg,#2b3038 0%,#3a3630 45%,#6b5236 72%,#2a2622 100%)}
.hero-title{top:190px;width:1200px;text-align:center;font-family:"Open Sans",sans-serif;font-weight:800;font-size:66px;color:var(--white)}
.hero-sub{top:282px;width:1200px;text-align:center;font-family:"Open Sans",sans-serif;font-weight:700;font-size:27px;color:var(--blue);letter-spacing:1px}
.hero-text{top:330px;left:185px;width:830px;text-align:center;font-size:15px;line-height:1.55;color:var(--white)}
.arrow{top:255px}

/* welcome */
.welcome-title{top:722px;width:1200px;text-align:center;font-size:42px}
.divider{top:775px;left:520px;width:160px;height:30px}
.welcome-text{top:820px;left:200px;width:800px;text-align:center;font-size:13.5px;line-height:1.65;color:#b1b1b1}

/* what is */
.what{top:943px;left:0;width:1200px;height:487px;background:linear-gradient(180deg,#3e3e3e,#4f5154 50%,#333 100%)}
.what-title{top:50px;width:1200px;text-align:center;font-family:"Montserrat",sans-serif;font-weight:700;font-size:40px;color:var(--white);letter-spacing:2px}
.what-text{top:120px;left:210px;width:780px;text-align:center;font-size:14.5px;line-height:1.6;color:#e2e2e2}
.card{top:242px;width:318px;height:192px;background:rgba(255,255,255,.72);text-align:center;padding:82px 24px 0}
.card.hi{background:var(--white)}
.card h3{font-family:"Open Sans",sans-serif;font-weight:600;font-size:21px;color:var(--ink);margin-bottom:10px}
.card p{font-size:12.5px;line-height:1.55;color:#666}
.card-icon{top:187px;width:110px;height:110px;border-radius:50%;background:#eaeaea;border:6px solid #cfcfcf;display:flex;align-items:center;justify-content:center}

/* lanterns & consultancy */
.lanterns{top:1495px;left:0;width:600px;height:415px;background:linear-gradient(135deg,#1f1f1f,#3a3a3a 60%,#262626)}
.lanterns h2{position:absolute;top:115px;left:138px;font-size:30px;color:var(--white)}
.lanterns p{position:absolute;top:168px;left:118px;width:380px;text-align:center;font-size:14.5px;line-height:1.6;color:#d8d8d8}
.consult-photo{top:1495px;left:600px;width:600px;height:415px;background:linear-gradient(135deg,#e8e6e1,#c9c4ba 45%,#6c7a8e 80%,#3c4a60)}
.consult-label{top:1852px;left:681px;font-size:30px;color:var(--white)}

/* vigil */
.vigil-photo{top:1945px;left:0;width:545px;height:370px;background:linear-gradient(110deg,#111 0%,#555 40%,#bdbdbd 75%,#eee 100%)}
.product-title{font-size:34px;color:var(--blue);letter-spacing:4px}
.product-text p{font-size:14.5px;line-height:1.55;color:#444;margin-bottom:16px}

/* kerbside */
.kerb-photo{top:2329px;left:752px;width:448px;height:398px;background:linear-gradient(120deg,#f4f4f4,#c8c8c8 45%,#595959 80%,#2a2a2a)}

/* expertise */
.expertise{top:2727px;left:0;width:1200px;height:339px;background:linear-gradient(180deg,#1d1d1d,#2c2c2c 50%,#1e1e1e)}
.expertise h2{position:absolute;top:90px;width:1200px;text-align:center;font-size:38px;color:var(--white)}
.expertise p{position:absolute;width:1200px;text-align:center;font-size:17px;color:#e6e6e6}

/* help */
.help-photo{top:3066px;left:575px;width:625px;height:537px;background:linear-gradient(160deg,#ffffff,#e6ebf1 45%,#c5ccd6 75%,#8d96a3)}
.help-title{top:3130px;left:109px;font-size:34px;color:var(--ink);letter-spacing:3px}
.help-item{left:112px;display:flex;gap:20px;align-items:flex-start;width:560px}
.help-icon{flex:none;width:78px;height:78px;border-radius:50%;border:3px solid #cfd6dd;background:var(--white);display:flex;align-items:center;justify-content:center}
.help-icon span{width:56px;height:56px;border-radius:50%;background:var(--blue-dark);display:flex;align-items:center;justify-content:center}
.help-item h4{font-weight:400;font-size:21px;line-height:1.35;color:var(--ink)}
.help-item p{font-size:13px;color:#666;line-height:1.5;margin-top:4px;width:340px}

/* contact */
.contact{top:3603px;left:0;width:1200px;height:504px;background:linear-gradient(180deg,#222,#343434 50%,#252525)}
.contact h2{position:absolute;top:55px;width:1200px;text-align:center;font-size:38px;color:var(--white)}
.contact .intro{position:absolute;top:122px;left:220px;width:760px;text-align:center;font-size:13.5px;line-height:1.65;color:#e2e2e2}
.field{position:absolute;left:118px;width:330px;height:52px;background:var(--white);color:#999;font-size:13px;padding:16px 16px}
.message{position:absolute;left:460px;top:182px;width:622px;height:174px;background:var(--white);color:#999;font-size:13px;padding:16px}
.submit{position:absolute;left:118px;top:377px;width:964px;height:50px;border:2px solid #bdbdbd;color:var(--white);font-size:17px;text-align:center;line-height:46px;letter-spacing:1px}

/* footer */
.footer{top:4107px;left:0;width:1200px;height:316px;background:#eeeeee}
.foot-head{position:absolute;font-family:"Montserrat",sans-serif;font-weight:800;font-size:20px;letter-spacing:3px;color:var(--blue)}
.post{position:absolute;left:80px;display:flex;gap:16px;width:330px}
.post .thumb{flex:none;width:48px;height:48px;border-radius:50%;background:linear-gradient(135deg,#a36b3c,#3b4a5e)}
.post p{font-size:13px;color:#555;line-height:1.45}
.post small{display:block;font-size:12px;color:var(--blue);margin-top:2px}
.foot-mark{position:absolute;left:548px;top:20px;width:104px;height:104px;border-radius:50%;background:var(--blue)}
.foot-name{position:absolute;top:160px;width:1200px;text-align:center;font-family:"Open Sans",sans-serif;font-weight:800;font-size:28px;letter-spacing:3px;color:var(--ink)}
.copy{position:absolute;top:212px;width:1200px;text-align:center;font-size:13.5px;color:#555}
.info{position:absolute;left:811px;display:flex;gap:16px;align-items:flex-start;font-size:13.5px;color:#666;line-height:1.45;width:320px}
</style>
</head>
<body>

<header class="abs header">
  <div class="abs brand"><span class="brand-mark"></span><span class="brand-name">KORVEL</span></div>
  <div class="abs contact-line" style="left:770px">
    <span class="ring"><svg width="16" height="16" viewBox="0 0 24 24"><path fill="#1d8fd6" d="M6.6 10.8a15 15 0 0 0 6.6 6.6l2.2-2.2c.3-.3.7-.4 1-.2 1.1.4 2.3.6 3.6.6.6 0 1 .4 1 1V20c0 .6-.4 1-1 1A17 17 0 0 1 3 4c0-.6.4-1 1-1h3.5c.6 0 1 .4 1 1 0 1.3.2 2.5.6 3.6.1.3 0 .7-.2 1z"/></svg></span>123 555 0142
  </div>
  <div class="abs contact-line" style="left:955px">
    <span class="ring"><svg width="16" height="16" viewBox="0 0 24 24"><path fill="none" stroke="#1d8fd6" stroke-width="2" d="M3 6h18v12H3zM3 6l9 7 9-7"/></svg></span>info@korvel.com
  </div>
  <nav class="abs nav">
    <a class="active" href="#" style="width:107px">Home</a>
    <a href="#" style="width:129px">About Us</a>
    <a href="#" style="width:115px">Lanterns</a>
    <a href="#" style="width:153px">Consultancy</a>
    <a href="#" style="width:101px">News</a>
    <a href="#">Contact Us</a>
  </nav>
</header>

<section class="abs hero" role="img" aria-label="Night city skyline photograph">
  <svg class="abs arrow" style="left:22px" width="24" height="48" viewBox="0 0 24 48"><path d="M20 4 4 24l16 20" fill="none" stroke="#fff" stroke-width="3"/></svg>
  <svg class="abs arrow" style="right:22px" width="24" height="48" viewBox="0 0 24 48"><path d="M4 4l16 20L4 44" fill="none" stroke="#fff" stroke-width="3"/></svg>
  <h1 class="abs hero-title" style="top:190px">KORVEL SOLUTIONS</h1>
  <p class="abs hero-sub" style="top:280px">Business Coaching &amp; Consulating For IT</p>
  <p class="abs hero-text">Lorem Ipsum is simply dummy text of the printing and typesetting industry. Lorem Ipsum has been the industry's standard dummy text ever since the 1500s, when an unknown printer took a galley of type.</p>
</section>

<h2 class="abs wide welcome-title">Welcome to <span class="blue">Korvel</span></h2>
<svg class="abs divider" viewBox="0 0 160 30"><line x1="0" y1="15" x2="160" y2="15" stroke="#cfcfcf" stroke-width="1.5"/><circle cx="80" cy="15" r="11" fill="#6f6f6f"/></svg>
<p class="abs welcome-text">Lorem ipsum is simply dummy text of the printing and typesetting industry. Lorem Ipsum has been the industry's standard dummy text ever since the 1500s, when an unknown printer took a galley of type and scrambled it to make a type specimen book. It has survived not only five centuries, but also the leap into electronic typesetting.</p>

<section class="abs what">
  <h2 class="abs what-title">WHAT IS <span class="blue">KORVEL</span></h2>
  <p class="abs what-text">Korvel Solutions is an IT consultancy firm with a difference. We can provide IT expertise for your business at any stage – from initial idea to live system.</p>
  <div class="abs card" style="left:80px"><h3>Software Development</h3><p>Lorem Ipsum is simply dummy text of the printing and typesetting industry. Lorem Ipsum has been the industry's standard...</p></div>
  <div class="abs card hi" style="left:433px;width:333px"><h3>IOT System Design</h3><p>Lorem Ipsum is simply dummy text of the printing and typesetting industry. Lorem Ipsum has been the industry's standard...</p></div>
  <div class="abs card" style="left:790px;width:330px"><h3>Machine learning solutions</h3><p>Lorem Ipsum is simply dummy text of the printing and typesetting industry. Lorem Ipsum has been the industry's standard...</p></div>
  <div class="abs card-icon" style="left:184px"><svg width="52" height="42" viewBox="0 0 52 42"><rect x="2" y="2" width="48" height="32" rx="3" fill="#555"/><rect x="6" y="8" width="40" height="22" fill="#fff"/><path d="M20 14l-5 5 5 5M32 14l5 5-5 5" stroke="#1d8fd6" stroke-width="2.5" fill="none"/><rect x="18" y="36" width="16" height="4" fill="#555"/></svg></div>
  <div class="abs card-icon" style="left:545px"><svg width="50" height="50" viewBox="0 0 50 50"><circle cx="25" cy="25" r="9" fill="#1d8fd6"/><g stroke="#1d8fd6" stroke-width="2"><line x1="25" y1="4" x2="25" y2="14"/><line x1="25" y1="36" x2="25" y2="46"/><line x1="4" y1="25" x2="14" y2="25"/><line x1="36" y1="25" x2="46" y2="25"/><line x1="10" y1="10" x2="17" y2="17"/><line x1="33" y1="33" x2="40" y2="40"/><line x1="40" y1="10" x2="33" y2="17"/><line x1="17" y1="33" x2="10" y2="40"/></g><g fill="#1d8fd6"><circle cx="25" cy="4" r="3"/><circle cx="25" cy="46" r="3"/><circle cx="4" cy="25" r="3"/><circle cx="46" cy="25" r="3"/></g></svg></div>
  <div class="abs card-icon" style="left:900px"><svg width="50" height="50" viewBox="0 0 50 50"><path d="M12 44V32c-5-4-6-9-6-13a17 17 0 0 1 34 0l4 8h-4v7h-8v10z" fill="#555"/><circle cx="24" cy="19" r="6" fill="none" stroke="#fff" stroke-width="3"/></svg></div>
</section>

<section class="abs lanterns" role="img" aria-label="Dark office workspace photograph">
  <h2 class="wide">Korvel Lanterns</h2>
  <p>Lorem Ipsum is simply dummy text of the printing and typesetting industry. Lorem Ipsum has been the industry's standard dummy text ever since the 1500s, when an unknown printer took a galley of type and scrambled it to make a type specimen book.</p>
</section>
<div class="abs consult-photo" role="img" aria-label="Photograph of two colleagues working at a laptop"></div>
<h2 class="abs wide consult-label">Korvel Consultancy</h2>

<div class="abs vigil-photo" role="img" aria-label="Black and white photograph of a driver holding a phone at the wheel"></div>
<h2 class="abs wide product-title" style="top:1985px;left:575px">VIGIL</h2>
<div class="abs product-text" style="top:2045px;left:575px;width:560px">
  <p>The primary cause of accidents on the road are caused by human error. Of these driver distraction and fatigue are the real problem.</p>
  <p>VIGIL is a system for HGV/HMT drivers to make every journey safer – safer for the driver and safer to other road users.</p>
  <p>VIGIL uses advanced deep learning techniques to monitor driver behavior in real time inside the cabin. VIGIL can detect driver distraction (mobile phone usage, smoking, failure to focused on the road ahead) and also monitor for classic signs of fatigue.</p>
</div>

<div class="abs kerb-photo" role="img" aria-label="Black and white photograph of a hand signing a document with a pen"></div>
<h2 class="abs wide product-title" style="top:2397px;left:80px">KERBSIDE</h2>
<div class="abs product-text" style="top:2452px;left:80px;width:630px">
  <p>Kerbside is a machine learning system that tracks and analyzes live used car trading markets. It learns every aspect of a car ads, through which, it creates powerful market intelligence for all parties in the used car ecosystem.</p>
  <p>It gives inexperienced buyers independent market consensus price, depreciation and approximated running costs for cars they are interested.</p>
  <p>It provides dealerships comprehensive market intelligence including demands, supply, consensus price, and expected market life of car.</p>
</div>

<section class="abs expertise" role="img" aria-label="Dark photograph of a desk with a laptop">
  <h2 class="wide">Strong Expertise</h2>
  <p style="top:165px;left:250px;width:700px">We have many years experience in machine learning, data mining, app development, DevOps and hardware design.</p>
  <p style="top:225px">We solve "hard" problems for business</p>
</section>

<div class="abs help-photo" role="img" aria-label="Photograph of a businessman in a suit beside a rising blue arrow chart"></div>
<h2 class="abs wide help-title">How we can help</h2>
<div class="abs help-item" style="top:3235px">
  <div class="help-icon"><span><svg width="32" height="24" viewBox="0 0 32 24"><path d="M2 4h18v14H2zM20 9h6l4 5v4H20z" fill="#fff"/><circle cx="8" cy="20" r="3" fill="#0f6fb0" stroke="#fff" stroke-width="2"/><circle cx="25" cy="20" r="3" fill="#0f6fb0" stroke="#fff" stroke-width="2"/></svg></span></div>
  <div><h4>Acquire more development capacity and get result fast</h4><p>Lorem Ipsum is simply dummy text of the printing and typesetting.</p></div>
</div>
<div class="abs help-item" style="top:3340px">
  <div class="help-icon"><span><svg width="26" height="32" viewBox="0 0 26 32"><path d="M9 2h8l-3 6h-2zM5 12c0-2 3-4 8-4s8 2 8 4c3 4 4 10 1 15-1 2-4 3-9 3s-8-1-9-3c-3-5-2-11 1-15z" fill="#fff"/><text x="13" y="25" font-size="12" font-weight="700" text-anchor="middle" fill="#0f6fb0" font-family="Poppins,sans-serif">$</text></svg></span></div>
  <div><h4 style="padding-top:8px">Avoid the overhead incurred by frequent scaling of your development team</h4></div>
</div>
<div class="abs help-item" style="top:3470px">
  <div class="help-icon"><span><svg width="30" height="30" viewBox="0 0 30 30"><circle cx="15" cy="11" r="7" fill="#fff"/><path d="M6 28c0-6 4-9 9-9s9 3 9 9z" fill="#fff"/></svg></span></div>
  <div><h4 style="padding-top:22px">Reach a wide spectrum of expertise</h4></div>
</div>

<section class="abs contact">
  <h2 class="wide">Contact us</h2>
  <p class="intro">Thank you for your interest in Korvel services. We are glad you stopped by. For additional information regarding our audit and professional services offerings, please fill out the contact form and we will contact you promptly.</p>
  <div class="field" style="top:182px">Name</div>
  <div class="field" style="top:245px">E - Mail</div>
  <div class="field" style="top:307px">Phone</div>
  <div class="message">Message</div>
  <div class="submit">SUBMIT</div>
</section>

<footer class="abs footer">
  <h3 class="foot-head" style="top:52px;left:80px">BLOG</h3>
  <div class="post" style="top:100px"><span class="thumb"></span><p>Lorem Ipsum is simply dummy text of the printing.<small>Today 5:40 pm - 15.05.2018</small></p></div>
  <div class="post" style="top:188px"><span class="thumb" style="background:linear-gradient(135deg,#b8c4d4,#3b4a5e)"></span><p>Lorem Ipsum is simply dummy text of the printing.<small>Today 2:20 pm - 15.05.2018</small></p></div>
  <span class="foot-mark"></span>
  <div class="foot-name">KORVEL</div>
  <div class="copy">© <span class="blue">KORVEL</span> – 2018. All Rights Reserved</div>
  <h3 class="foot-head" style="top:52px;left:811px">CONTACT INFO</h3>
  <div class="info" style="top:102px"><svg width="20" height="24" viewBox="0 0 20 24"><path d="M10 1a8 8 0 0 0-8 8c0 6 8 14 8 14s8-8 8-14a8 8 0 0 0-8-8z" fill="none" stroke="#888" stroke-width="2"/><circle cx="10" cy="9" r="3" fill="#888"/></svg><span>PO Box 1234, Street Name, City Name, Country 123456.</span></div>
  <div class="info" style="top:158px"><svg width="20" height="20" viewBox="0 0 24 24"><path fill="#888" d="M6.6 10.8a15 15 0 0 0 6.6 6.6l2.2-2.2c.3-.3.7-.4 1-.2 1.1.4 2.3.6 3.6.6.6 0 1 .4 1 1V20c0 .6-.4 1-1 1A17 17 0 0 1 3 4c0-.6.4-1 1-1h3.5c.6 0 1 .4 1 1 0 1.3.2 2.5.6 3.6.1.3 0 .7-.2 1z"/></svg><span class="blue">123 555 0190</span></div>
  <div class="info" style="top:202px"><svg width="20" height="18" viewBox="0 0 24 20"><path fill="none" stroke="#888" stroke-width="2" d="M2 2h20v16H2zM2 2l10 8 10-8"/></svg><span>info@korvel.com</span></div>
</footer>

</body>
</html>
```